Heritage Hollow Business Cards

Require a business card design. <br/><br/>Needs to include logo (either round or long version) plus these details:<br/>Maya Torvell<br/>Heritage Hollow<br/>maya@kelvadtrading.com.au<br/>02 6481 7395<br/>PO Box Glenwarra NSW 2791<br/>www.heritagehollow.com.au<br/><br/>I need in an editable format so that I can create for multiple staff members. <br/><br/>

Target Market(s)

We are an online store selling renovation products to home owners are builders. Looking for a classic classy design.

Industry/Entity Type

Home And Garden

Contact Information for Business Card

Maya Torvell
Heritage Hollow
maya@kelvadtrading.com.au
02 6481 7395
PO Box Glenwarra NSW 2791
www.heritagehollow.com.au

Colors

Designer to choose colors to be used in the design.

Requirements
Must have
• Must include Logo.

```html
<!DOCTYPE html>
<html lang="en">
<head>
<meta charset="utf-8">
<title>Heritage Hollow Business Cards</title>
<link href="https://fonts.googleapis.com/css2?family=Alegreya:wght@500&family=Roboto:wght@300;400;500&display=swap" rel="stylesheet">
<style>
  :root {
    --page: #e4e4e6;
    --card-dark: #0c0c0c;
    --card-dark-edge: #161616;
    --card-light: #ededed;
    --brand-faint: #3e3e3e;
    --ink: #1a1a1a;
    --ink-soft: #2b2b2b;
  }
  * { margin: 0; padding: 0; box-sizing: border-box; }
  html, body { width: 1200px; height: 1200px; overflow: hidden; }
  body { background: var(--page); position: relative; font-family: "Roboto", sans-serif; }

  .card { position: absolute; width: 662px; height: 378px; border-radius: 14px; overflow: hidden; }

  .card-front { left: 269px; top: 178px; background: radial-gradient(ellipse at 60% 30%, var(--card-dark-edge), var(--card-dark) 70%); }
  .front-brand {
    position: absolute; left: 150px; top: 198px;
    font-family: "Roboto", sans-serif; font-weight: 500; font-size: 44px;
    color: var(--brand-faint); letter-spacing: 0.5px; line-height: 1;
  }

  .card-back { left: 271px; top: 643px; background: var(--card-light); }
  .brand-mark {
    position: absolute; left: 412px; top: 24px; width: 192px; height: 192px;
    border: 1.2px solid var(--ink); border-radius: 50%;
    display: flex; align-items: center; justify-content: center; text-align: center;
  }
  .brand-name {
    font-family: "Roboto", sans-serif; font-weight: 500; font-size: 26px;
    line-height: 1.1; color: var(--ink);
  }

  .person-name {
    position: absolute; left: 47px; top: 218px;
    font-family: "Alegreya", serif; font-weight: 500; font-size: 27px;
    color: var(--ink-soft); letter-spacing: 0.3px; text-transform: uppercase;
  }
  .contact-block {
    position: absolute; left: 48px; top: 268px; height: 89px;
    border-left: 1.2px solid var(--ink-soft); padding-left: 15px;
  }
  .company { font-weight: 500; font-size: 15px; color: var(--ink); line-height: 18px; margin-top: -4px; }
  .contact-list { list-style: none; margin-top: 2px; }
  .contact-list li {
    display: flex; align-items: center; gap: 5px;
    font-weight: 300; font-size: 12px; color: var(--ink); height: 18.5px;
  }
  .contact-list svg { width: 9px; height: 9px; flex: none; fill: var(--ink); }
  .contact-list b { font-weight: 500; }
</style>
</head>
<body>
  <section class="card card-front" aria-label="Card front">
    <div class="front-brand">Heritage Hollow</div>
  </section>

  <section class="card card-back" aria-label="Card back">
    <div class="brand-mark">
      <div class="brand-name">Heritage<br>Hollow</div>
    </div>

    <h1 class="person-name">Maya Torvell</h1>

    <div class="contact-block">
      <p class="company">HERITAGE HOLLOW</p>
      <ul class="contact-list">
        <li><svg viewBox="0 0 10 10"><path d="M5 0a3.5 3.5 0 0 0-3.5 3.5C1.5 6 5 10 5 10s3.5-4 3.5-6.5A3.5 3.5 0 0 0 5 0zm0 4.8a1.3 1.3 0 1 1 0-2.6 1.3 1.3 0 0 1 0 2.6z"/></svg>PO Box Glenwarra NSW 2791</li>
        <li><svg viewBox="0 0 10 10"><path d="M2 .5l1.6 2-1 1.2a6 6 0 0 0 3.7 3.7l1.2-1 2 1.6-.9 1.5C4.8 9.7.3 5.2.5 1.4z"/></svg>02 6481 7395</li>
        <li><svg viewBox="0 0 10 10"><path d="M0 2h10v6H0zm1 .8v.3l4 2.6 4-2.6v-.3z"/></svg>maya@kelvadtrading.com.au</li>
        <li><svg viewBox="0 0 10 10"><path d="M5 0a5 5 0 1 0 0 10A5 5 0 0 0 5 0zm0 1c.6.6 1.1 1.9 1.2 3.5H3.8C3.9 2.9 4.4 1.6 5 1zM1 5.5h1.8c.1 1.3.4 2.4.9 3.2A4 4 0 0 1 1 5.5zm0-1a4 4 0 0 1 2.7-3.2c-.5.8-.8 1.9-.9 3.2zm4 4.5c-.6-.6-1.1-1.9-1.2-3.5h2.4C6.1 7.1 5.6 8.4 5 9zm1.3-.3c.5-.8.8-1.9.9-3.2H9a4 4 0 0 1-2.7 3.2zm.9-4.2c-.1-1.3-.4-2.4-.9-3.2A4 4 0 0 1 9 4.5z"/></svg>www.<b>heritagehollow</b>.com.au</li>
      </ul>
    </div>
  </section>
</body>
</html>
```